50 years of Beat (birthday party)

I need a flyer that I can send to all guests as ChatLoop.
Also as a digital file (e.g. PDF). Thanks!
Occasion: Beat's 50th birthday
It's a birthday party for family and friends
Location: Marquee at the sports ground, 7345 Tallwil
Live music
Bar pub
Corrabeg
Date: Saturday, May 25, 2024
Time: from 2 p.m. until open-end
Flexible participation - come and go as you please
Registration or deregistration: ChatLoop on 078 - 512 63 17

Please create a flyer as an invitation. I want an Irish rock style with a touch of “Schlager” :-). There should be a real party.
Attention: no heavy metal style!!
It would be cool if a rock guitar and/or microphone were included.
Otherwise, I'm free and happy to be surprised. The flyer should not be too childish or youthful. There are practically no children at the event.

Additionally, please send a simpler flyer than “Save the date”.
Just the date and occasion.
Without place, time and registration.
With the note: Update follows...
The design is the same as the flyer with registration.
Updates

It would be cool if the Corrabeg logo was visible too.
A whiskey glass would also be possible.
Balloons are not absolutely necessary - it looks like a children's party.
Please make the flyers rocky.

Target Market(s)

Family & Friends

Industry/Entity Type

look

Font styles to use
Other font styles liked:
• rockig

Colors

Designer to choose colors to be used in the design.

Requirements
Must have
• Irish rock design
Nice to have
• Rock guitar would be cool
Should not have
• comics

```html
<!DOCTYPE html>
<html lang="en">
<head>
<meta charset="utf-8">
<title>Beat's 50th Birthday – Invitation</title>
<link href="https://fonts.googleapis.com/css2?family=Montserrat:wght@400;500;700;800;900&family=Roboto+Condensed:wght@700;800&family=Kaushan+Script&display=swap" rel="stylesheet">
<style>
  :root {
    --stage: #18531a;
    --flyer-dark: #020c03;
    --flyer-glow: #0d4410;
    --green: #74b843;
    --green-deep: #2f6e24;
    --white: #ffffff;
    --dot: #2d7a2a;
  }
  * { margin: 0; padding: 0; box-sizing: border-box; }
  html, body { width: 1200px; height: 1200px; overflow: hidden; }
  body { background: var(--stage); position: relative; }

  .flyer {
    position: absolute; left: 191px; top: 20px; width: 818px; height: 1160px;
    background:
      radial-gradient(ellipse 55% 40% at 60% 52%, var(--flyer-glow) 0%, rgba(13,68,16,0.4) 45%, rgba(2,12,3,0) 80%),
      var(--flyer-dark);
    overflow: hidden;
    font-family: "Roboto Condensed", "Arial Narrow", sans-serif;
    color: var(--white);
  }

  .frame { position: absolute; inset: 0; }

  .corner-ornament {
    position: absolute; width: 104px; height: 104px;
    background: radial-gradient(circle at 50% 50%, rgba(116,184,67,0.45), rgba(47,110,36,0.25) 60%, rgba(0,0,0,0) 75%);
    border-radius: 18px;
  }
  .corner-ornament.tl { left: 38px; top: 44px; }
  .corner-ornament.tr { right: 38px; top: 44px; }
  .corner-ornament.bl { left: 38px; bottom: 44px; }
  .corner-ornament.br { right: 38px; bottom: 44px; }

  .intro { position: absolute; left: 0; width: 100%; text-align: center; font-family: "Montserrat", sans-serif; }
  .intro-line1 { top: 143px; font-size: 19px; font-weight: 400; letter-spacing: 7.5px; color: var(--white); }
  .intro-line2 { top: 167px; font-size: 19px; font-weight: 700; letter-spacing: 7px; color: var(--green); }

  .guitar-photo {
    position: absolute; left: 412px; top: 242px; width: 291px; height: 522px;
    background:
      radial-gradient(ellipse 60% 35% at 40% 72%, #1f8a2a 0%, #0f5a18 45%, rgba(10,60,16,0) 80%),
      linear-gradient(160deg, rgba(40,120,40,0.25), rgba(5,40,10,0.1));
    border-radius: 30px;
  }

  .name { position: absolute; left: 176px; top: 248px; font-family: "Montserrat", sans-serif; font-weight: 900; font-size: 74px; color: var(--green); letter-spacing: 1px; line-height: 1; }
  .age { position: absolute; left: 172px; top: 326px; font-family: "Montserrat", sans-serif; font-weight: 800; color: var(--white); line-height: 1; }
  .age-number { font-size: 112px; letter-spacing: -3px; }
  .age-suffix { font-size: 66px; vertical-align: 40px; margin-left: 2px; }
  .script-title {
    position: absolute; left: 165px; top: 420px; font-family: "Kaushan Script", cursive;
    font-size: 122px; color: var(--green); transform: rotate(-13deg); transform-origin: left center; line-height: 1;
  }

  .when { position: absolute; left: 189px; font-weight: 700; line-height: 1; }
  .when.white { color: var(--white); }
  .when.green { color: var(--green); }
  .day { top: 608px; font-size: 33px; }
  .date { top: 641px; font-size: 33px; }
  .from { top: 700px; font-size: 33px; }
  .until { top: 733px; font-size: 33px; }

  .dots { position: absolute; height: 0; border-top: 3px dotted var(--dot); }
  .dots.d1 { left: 189px; top: 686px; width: 223px; }
  .dots.d2 { left: 189px; top: 785px; width: 419px; }
  .dots.d3 { left: 189px; top: 827px; width: 419px; }
  .dots.d4 { left: 145px; top: 928px; width: 518px; }
  .dots.d5 { left: 145px; top: 961px; width: 518px; }
  .vdots { position: absolute; top: 848px; height: 62px; border-left: 3px dotted var(--dot); }
  .vdots.v1 { left: 316px; }
  .vdots.v2 { left: 465px; }

  .venue { position: absolute; left: 189px; width: 419px; top: 795px; text-align: center; font-size: 23px; font-weight: 700; }

  .feature { position: absolute; top: 846px; font-size: 35px; font-weight: 700; line-height: 0.95; }
  .feature.music { left: 190px; }
  .feature.bar { left: 368px; }
  .sponsor { position: absolute; left: 490px; top: 868px; display: flex; align-items: center; gap: 7px; font-family: "Roboto Condensed", sans-serif; font-weight: 700; font-size: 28px; color: var(--white); }
  .sponsor-dot { width: 12px; height: 12px; border-radius: 50%; background: var(--white); }

  .note { position: absolute; left: 0; width: 100%; top: 935px; text-align: center; font-size: 16px; font-weight: 700; letter-spacing: 2.6px; color: var(--green); }
  .rsvp { position: absolute; left: 0; width: 100%; text-align: center; font-size: 31px; font-weight: 700; letter-spacing: 2.6px; line-height: 1; }
  .rsvp.r1 { top: 979px; }
  .rsvp.r2 { top: 1013px; }
</style>
</head>
<body>
<main class="flyer">
  <svg class="frame" width="818" height="1160" viewBox="0 0 818 1160" aria-hidden="true">
    <g fill="none" stroke="var(--green)">
      <rect x="60" y="66" width="698" height="1028" stroke-width="2.5"/>
      <rect x="69" y="75" width="680" height="1010" stroke-width="1.2"/>
      <rect x="78" y="84" width="662" height="992" stroke-width="1.2" stroke="var(--green-deep)"/>
    </g>
  </svg>
  <div class="corner-ornament tl" role="img" aria-label="Celtic knot corner ornament"></div>
  <div class="corner-ornament tr" role="img" aria-label="Celtic knot corner ornament"></div>
  <div class="corner-ornament bl" role="img" aria-label="Celtic knot corner ornament"></div>
  <div class="corner-ornament br" role="img" aria-label="Celtic knot corner ornament"></div>

  <p class="intro intro-line1">IT'S A BIRTHDAY PARTY FOR</p>
  <p class="intro intro-line2">FAMILY AND FRIENDS</p>

  <div class="guitar-photo" role="img" aria-label="Photo of a green flame-top electric guitar with a glass of whiskey on the rocks"></div>

  <h1 class="name">BEAT'S</h1>
  <p class="age"><span class="age-number">50</span><span class="age-suffix">TH</span></p>
  <p class="script-title">Birthday</p>

  <p class="when white day">SATURDAY,</p>
  <p class="when green date">MAY 25,2024</p>
  <div class="dots d1"></div>
  <p class="when white from">FROM 2 P.M.</p>
  <p class="when green until">UNTIL OPEN-END</p>

  <div class="dots d2"></div>
  <p class="venue">Marquee at the sports ground, 7345 Tallwil</p>
  <div class="dots d3"></div>

  <p class="feature music">Live<br>Music</p>
  <div class="vdots v1"></div>
  <p class="feature bar">Bar<br>Pub</p>
  <div class="vdots v2"></div>
  <p class="sponsor"><span class="sponsor-dot"></span>CORRABEG</p>

  <div class="dots d4"></div>
  <p class="note">FLEXIBLE PARTICIPATION - COME AND GO AS YOU PLEASE</p>
  <div class="dots d5"></div>

  <p class="rsvp r1">REGISTRATION OR DEREGISTRATION</p>
  <p class="rsvp r2">CHATLOOP ON 078 - 512 63 17</p>
</main>
</body>
</html>
```